Create a Stalvik-looking dashboard for our Open Compass Speedometer that can look similar to my AI-generated dashboard attached, but with: 1) clear borders on all four sides, 2) is created in a way that we can modify the numbers weekly, say maybe you create the graphic that we can inset the excel spreadsheet numbers into, but ideally mixed with the Stalvik look black leather bubble design shown in the dashboard?; 3) uses the exact numbers shown in the attachment; 4) the speedometer on top should have four equal colors of red on left (-1), then yellow (0), then light green (1), then medium green (2); 5) the gauge on the top left should be the graphic that includes 0-100% bar that is currently 33%, and right below that a -20 to +20 bar with the arrow pointing to 11.9%, with color coding similar to the graphic; 6) replace the Stalvik logo in the middle with a similar shaped shield with blue background with the "T" logo with the eagle inside it, like attached

```html
<!DOCTYPE html>
<html lang="en">
<head>
<meta charset="utf-8">
<title>Open Compass Speedometer</title>
<link href="https://fonts.googleapis.com/css2?family=Cinzel:wght@700;900&family=Play:wght@400;700&display=swap" rel="stylesheet">
<style>
  :root{
    --bg:#000;
    --leather:#b3161c;
    --leather-dark:#5e0b0f;
    --cabin:#2a2a2e;
    --panel:#111114;
    --panel-edge:#8d8d92;
    --pod:#123a3c;
    --gold:#d9a93f;
    --amber:#f2c232;
    --text:#f4f1e8;
    --ink:#111;
    --red:#b1231f;
    --red-bright:#e03126;
    --yellow:#e6e05a;
    --lime:#97a740;
    --green:#3f5a27;
    --tan:#bba77f;
    --sand:#efcf9b;
    --grey:#b4aca2;
    --grey-dark:#736c69;
  }
  html,body{margin:0;padding:0;width:1200px;height:1200px;overflow:hidden;background:var(--bg);}
  .dashboard{display:block;width:1200px;height:1200px;}
  .t{font-family:'Play',sans-serif;font-weight:700;fill:var(--text);text-anchor:middle;letter-spacing:1px;}
  .t-dark{fill:var(--ink);}
  .t-amber{fill:var(--amber);}
  .t-red{fill:var(--red);}
  .t-small{font-family:'Play',sans-serif;font-size:7px;fill:#6f8a8a;text-anchor:middle;letter-spacing:.5px;}
  .title{font-family:'Cinzel',serif;font-weight:900;font-size:29px;fill:var(--gold);text-anchor:middle;letter-spacing:1px;}
  .gauge-num{font-family:'Play',sans-serif;font-size:22px;fill:#111;text-anchor:middle;}
  .brand{font-family:'Play',sans-serif;font-weight:700;font-size:11px;fill:var(--text);text-anchor:middle;letter-spacing:1px;}
</style>
</head>
<body>
<svg class="dashboard" viewBox="0 0 1200 1200" xmlns="http://www.w3.org/2000/svg">
  <defs>
    <linearGradient id="cabinGrad" x1="0" y1="0" x2="0" y2="1">
      <stop offset="0" stop-color="#1c1c20"/>
      <stop offset=".35" stop-color="var(--leather)"/>
      <stop offset=".8" stop-color="var(--leather-dark)"/>
      <stop offset="1" stop-color="#5a5a60"/>
    </linearGradient>
    <radialGradient id="podGrad" cx=".5" cy=".6" r=".6">
      <stop offset="0" stop-color="#0a0c0d"/>
      <stop offset=".75" stop-color="#0d1d1f"/>
      <stop offset="1" stop-color="var(--pod)"/>
    </radialGradient>
    <linearGradient id="fadeGreen" x1="0" y1="0" x2="1" y2="1">
      <stop offset="0" stop-color="#a9d06c"/>
      <stop offset="1" stop-color="#f3f0d8"/>
    </linearGradient>
    <linearGradient id="redFade" x1="0" y1="0" x2="1" y2="0">
      <stop offset="0" stop-color="#4a0f12"/>
      <stop offset=".4" stop-color="var(--red-bright)"/>
      <stop offset="1" stop-color="var(--red-bright)"/>
    </linearGradient>
  </defs>

  <!-- cabin backdrop -->
  <rect class="cabin" x="0" y="190" width="1200" height="825" fill="url(#cabinGrad)" role="img" aria-label="Red leather sports car cabin interior with air vents around the instrument cluster"/>

  <!-- instrument cluster housing -->
  <path class="cluster" d="M95 520 Q100 370 200 335 L400 330 Q420 200 617 195 Q815 200 835 330 L1020 335 Q1120 370 1125 520 Q1125 555 1080 560 L140 560 Q95 555 95 520Z" fill="var(--panel)" stroke="var(--leather-dark)" stroke-width="3"/>

  <!-- left pod -->
  <path class="pod" d="M165 530 Q170 340 405 330 L405 470 Q330 505 260 540 L175 540Z" fill="url(#podGrad)" stroke="#cfd2d4" stroke-width="2"/>
  <circle cx="244" cy="430" r="48" fill="#0b0b0b" stroke="#e5e5e5" stroke-width="16"/>
  <path d="M244 382 A48 48 0 0 0 201.9 453.1" fill="none" stroke="var(--red-bright)" stroke-width="16"/>
  <line x1="247" y1="370" x2="246" y2="422" stroke="var(--red-bright)" stroke-width="3"/>
  <text class="t" x="244" y="436" font-size="10">33%</text>
  <text class="t" x="244" y="447" font-size="9">(165/500)</text>
  <text class="t-small" x="230" y="497">Companies</text>
  <text class="t-small" x="230" y="506">Reporting QTD</text>
  <circle cx="344" cy="414" r="28" fill="#0b0b0b" stroke="#58a852" stroke-width="6"/>
  <path d="M317.7 423.6 A28 28 0 0 0 370.3 423.6" fill="none" stroke="var(--red-bright)" stroke-width="6"/>
  <text class="t" x="344" y="420" font-size="12">75%</text>
  <text class="t-small" x="344" y="461">Companies Beating</text>
  <text class="t-small" x="344" y="470">Earnings Estimates</text>

  <!-- right pod -->
  <path class="pod" d="M1035 530 Q1030 340 815 330 L815 470 Q890 505 960 540 L1025 540Z" fill="url(#podGrad)" stroke="#cfd2d4" stroke-width="2"/>
  <path d="M859.5 399.1 A80 80 0 0 1 918 365.3" fill="none" stroke="#5fb055" stroke-width="10"/>
  <path d="M918 365.3 A80 80 0 0 1 981.6 388.4" fill="none" stroke="url(#fadeGreen)" stroke-width="10"/>
  <path d="M981.6 388.4 A80 80 0 0 1 1004.7 452" fill="none" stroke="#eee34a" stroke-width="10"/>
  <path d="M1004.7 452 A80 80 0 0 1 994.3 485" fill="none" stroke="#e9a53a" stroke-width="10"/>
  <path d="M994.3 485 A80 80 0 0 1 970.9 510.5" fill="none" stroke="var(--red-bright)" stroke-width="10"/>
  <line x1="921" y1="447" x2="902" y2="352" stroke="var(--red-bright)" stroke-width="3"/>
  <text class="t" x="838" y="416" font-size="9">20%</text>
  <text class="t" x="925" y="365" font-size="9">10%</text>
  <text class="t" x="994" y="387" font-size="9">0%</text>
  <text class="t" x="1027" y="447" font-size="9">-10%</text>
  <text class="t" x="1014" y="518" font-size="9">-20%</text>
  <text class="t-small" x="946" y="438" font-size="9">EPS</text>
  <text class="t-small" x="946" y="448" font-size="9">Growth</text>
  <text class="t" x="925" y="476" font-size="20">11.9%</text>

  <!-- centre gear gauge -->
  <path d="M617 432 L422 432 A195 195 0 0 1 479.1 294.1Z" fill="var(--red)"/>
  <path d="M617 432 L479.1 294.1 A195 195 0 0 1 617 237Z" fill="var(--yellow)"/>
  <path d="M617 432 L617 237 A195 195 0 0 1 754.9 294.1Z" fill="var(--lime)"/>
  <path d="M617 432 L754.9 294.1 A195 195 0 0 1 812 432Z" fill="var(--green)"/>
  <path d="M447 432 A170 170 0 0 1 787 432" fill="none" stroke="#111" stroke-width="10" stroke-dasharray="2 12"/>
  <path d="M413 432 A204 204 0 0 1 821 432" fill="none" stroke="#cfd2d4" stroke-width="3"/>
  <text class="gauge-num" x="478" y="382">-1</text>
  <text class="gauge-num" x="560" y="300">0</text>
  <text class="gauge-num" x="674" y="300">1</text>
  <text class="gauge-num" x="756" y="382">2</text>
  <circle cx="606" cy="330" r="6" fill="var(--text)"/>
  <text class="brand" x="622" y="334">OPEN COMPASS</text>
  <line x1="617" y1="432" x2="722" y2="298" stroke="#f0193c" stroke-width="5" stroke-linecap="round"/>
  <path d="M577 432 A40 40 0 0 1 657 432Z" fill="#1a1a1c" stroke="#666" stroke-width="2"/>
  <circle cx="617" cy="432" r="6" fill="#f0193c"/>
  <path d="M440 440 L617 432 L795 440 L760 460 L470 460Z" fill="#232326"/>

  <text class="title" x="605" y="520">OPEN COMPASS SPEEDOMETER</text>

  <!-- data table panel -->
  <rect x="238" y="540" width="744" height="250" rx="18" fill="var(--panel)" stroke="var(--panel-edge)" stroke-width="3"/>
  <g class="trend-table">
    <text class="t t-amber" x="400" y="560" font-size="13">GEAR</text>
    <text class="t t-amber" x="605" y="560" font-size="13">CURRENT TREND</text>
    <text class="t t-amber" x="843" y="560" font-size="13">LAST TREND CHANGE</text>

    <rect x="245" y="567" width="57" height="19" fill="var(--amber)"/><rect x="303" y="567" width="169" height="19" fill="var(--amber)"/>
    <rect x="474" y="567" width="276" height="19" fill="var(--tan)"/><rect x="753" y="567" width="217" height="19" fill="var(--tan)"/>
    <text class="t t-dark" x="289" y="581" font-size="12">2</text><text class="t t-dark" x="395" y="581" font-size="12">TURBO BOOST</text>
    <text class="t t-dark" x="605" y="581" font-size="12">BULL</text><text class="t t-dark" x="858" y="581" font-size="12">Friday, August 15,2014</text>

    <rect x="248" y="589" width="54" height="19" fill="var(--lime)"/><rect x="303" y="589" width="169" height="19" fill="var(--lime)"/>
    <rect x="474" y="589" width="276" height="19" fill="var(--grey)"/><rect x="753" y="589" width="214" height="19" fill="var(--grey)"/>
    <text class="t t-dark" x="289" y="604" font-size="12">1</text><text class="t t-dark" x="395" y="604" font-size="12">ACCELERATOR PEDAL</text>
    <text class="t t-dark" x="605" y="604" font-size="12">BULLISH</text>

    <rect x="251" y="610" width="51" height="19" fill="#f2e338"/><rect x="303" y="610" width="169" height="19" fill="#f2e338"/>
    <rect x="474" y="610" width="276" height="19" fill="var(--grey)"/><rect x="753" y="610" width="211" height="19" fill="var(--grey)"/>
    <text class="t t-dark" x="289" y="624" font-size="12">0</text><text class="t t-dark" x="395" y="624" font-size="12">BRAKES</text>
    <text class="t t-dark" x="605" y="624" font-size="12">BEARISH</text>

    <rect x="255" y="631" width="47" height="19" fill="var(--red)"/><rect x="303" y="631" width="169" height="19" fill="var(--red)"/>
    <rect x="474" y="631" width="276" height="19" fill="var(--grey-dark)"/><rect x="753" y="631" width="207" height="19" fill="var(--grey-dark)"/>
    <text class="t t-dark" x="289" y="646" font-size="12">-1</text><text class="t t-dark" x="395" y="645" font-size="12">REVERSE</text>
    <text class="t t-dark" x="605" y="646" font-size="12">BEAR</text>
  </g>

  <g class="gear-stats">
    <text class="t t-amber" x="400" y="667" font-size="13">GEAR</text>
    <text class="t t-amber" x="526" y="667" font-size="13">Total Days</text>
    <text class="t t-amber" x="620" y="667" font-size="13">Percent</text>
    <text class="t t-amber" x="738" y="667" font-size="13">$ invested</text>
    <text class="t t-amber" x="883" y="661" font-size="8">BRX50 Anual Return</text>
    <text class="t t-amber" x="883" y="671" font-size="8">Gain/Loss</text>

    <rect x="265" y="675" width="37" height="20" fill="#6a8a3a"/><rect x="303" y="675" width="169" height="20" fill="#6a8a3a"/>
    <rect x="474" y="675" width="101" height="20" fill="#d4c1a0"/><rect x="577" y="675" width="88" height="20" fill="#cdd08a"/>
    <rect x="667" y="675" width="143" height="20" fill="var(--tan)"/><rect x="812" y="675" width="140" height="20" fill="#1a1a1a"/>
    <text class="t t-dark" x="289" y="686" font-size="11">2</text><text class="t t-dark" x="395" y="690" font-size="12">TURBO BOOST</text>
    <text class="t t-dark" x="526" y="689" font-size="10">3,564</text><text class="t t-dark" x="621" y="689" font-size="10">69.11%</text>
    <text class="t t-dark" x="738" y="689" font-size="10">$779,158</text><text class="t" x="880" y="689" font-size="10">15.08%</text>

    <rect x="270" y="697" width="32" height="20" fill="#a7942e"/><rect x="303" y="697" width="169" height="20" fill="#a7942e"/>
    <rect x="474" y="697" width="101" height="20" fill="var(--sand)"/><rect x="577" y="697" width="88" height="20" fill="#f2e338"/>
    <rect x="667" y="697" width="143" height="20" fill="var(--sand)"/><rect x="812" y="697" width="137" height="20" fill="#2c1a18"/>
    <text class="t t-dark" x="289" y="711" font-size="11">1</text><text class="t t-dark" x="395" y="712" font-size="12">ACCELERATOR PEDAL</text>
    <text class="t t-dark" x="526" y="711" font-size="10">547</text><text class="t t-dark" x="621" y="711" font-size="10">10.62%</text>
    <text class="t t-dark" x="738" y="711" font-size="10">$249,993</text><text class="t" x="880" y="711" font-size="10">0.84%</text>

    <rect x="274" y="719" width="28" height="20" fill="var(--red)"/><rect x="303" y="719" width="169" height="20" fill="var(--red)"/>
    <rect x="474" y="719" width="101" height="20" fill="var(--sand)"/><rect x="577" y="719" width="88" height="20" fill="#f2e338"/>
    <rect x="667" y="719" width="143" height="20" fill="var(--sand)"/><rect x="812" y="719" width="134" height="20" fill="#4a1416"/>
    <text class="t t-dark" x="289" y="730" font-size="11">0</text><text class="t t-dark" x="395" y="733" font-size="12">BRAKES</text>
    <text class="t t-dark" x="526" y="733" font-size="10">937</text><text class="t t-dark" x="621" y="733" font-size="10">18.17%</text>
    <text class="t t-red" x="738" y="733" font-size="10">$82,11</text><text class="t" x="878" y="733" font-size="10">-8.16%</text>

    <rect x="278" y="741" width="24" height="20" fill="var(--red)"/><rect x="303" y="741" width="169" height="20" fill="var(--red)"/>
    <rect x="474" y="741" width="101" height="20" fill="#cbbfa9"/><rect x="577" y="741" width="88" height="20" fill="#d6c17a"/>
    <rect x="667" y="741" width="143" height="20" fill="#cbbfa9"/><rect x="812" y="741" width="130" height="20" fill="var(--red)"/>
    <text class="t t-dark" x="289" y="755" font-size="11">-1</text><text class="t t-dark" x="395" y="754" font-size="12">REVERSE</text>
    <text class="t t-dark" x="526" y="755" font-size="10">129</text><text class="t t-dark" x="621" y="755" font-size="10">2.49%</text>
    <text class="t t-red" x="738" y="755" font-size="10">$55,344</text><text class="t" x="878" y="755" font-size="10">20.53%</text>

    <text class="t t-amber" x="400" y="777" font-size="13">TOTAL</text>
    <text class="t" x="526" y="777" font-size="10">5,137</text>
    <text class="t t-amber" x="680" y="778" font-size="9">BRX50 Anual Averages Drawdown</text>
  </g>

  <!-- signal matrix -->
  <path d="M255 812 L960 812 L945 962 L270 962Z" fill="#3e3e42" stroke="var(--panel-edge)" stroke-width="2"/>
  <g class="signal-matrix">
    <rect x="285" y="816" width="182" height="26" fill="#14201a"/>
    <rect x="469" y="816" width="266" height="26" fill="#5a4f1c"/>
    <rect x="737" y="816" width="208" height="26" fill="#4a1012"/>
    <text class="t" x="367" y="834" font-size="12">TURBO BOOST(BULL)</text>
    <text class="t" x="600" y="834" font-size="12">ACCELERATOR PEDAL (BULLISH)</text>
    <text class="t" x="830" y="834" font-size="12">BRAKES(BEARISH)</text>

    <rect x="265" y="845" width="202" height="27" fill="#4f6a34"/>
    <rect x="469" y="845" width="266" height="27" fill="#e0b631"/>
    <rect x="737" y="845" width="208" height="27" fill="url(#redFade)"/>
    <text class="t t-dark" x="367" y="863" font-size="13">DELTA/V*</text>
    <text class="t t-dark" x="600" y="863" font-size="13">CALENDAR +</text>
    <text class="t" x="830" y="863" font-size="13">NEGATIVE</text>

    <rect x="263" y="874" width="204" height="27" fill="#4f6a34"/>
    <rect x="469" y="874" width="266" height="27" fill="#e0b631"/>
    <rect x="737" y="874" width="210" height="27" fill="var(--red-bright)"/>
    <text class="t t-dark" x="367" y="893" font-size="13">CALENDAR +</text>
    <text class="t t-dark" x="600" y="893" font-size="13">TURBO +</text>
    <text class="t" x="830" y="893" font-size="13">NEGATIVE</text>

    <rect x="265" y="903" width="202" height="26" fill="#4f6a34"/>
    <rect x="469" y="903" width="266" height="26" fill="#e0b631"/>
    <rect x="737" y="903" width="208" height="26" fill="var(--red-bright)"/>
    <text class="t t-dark" x="367" y="921" font-size="13">TURBO +</text>
    <text class="t t-red" x="600" y="921" font-size="13">TURBO -</text>
    <text class="t" x="830" y="921" font-size="13">NEGATIVE</text>

    <rect x="285" y="931" width="182" height="28" fill="#1e1e1e"/>
    <rect x="469" y="931" width="266" height="28" fill="#4e4315"/>
    <rect x="737" y="931" width="190" height="28" fill="#3a1012"/>
    <text class="t" x="367" y="952" font-size="16" fill="#d6d0c2">REVERSE -</text>
    <text class="t" x="612" y="952" font-size="16" fill="#d6d0c2">REVERSE -</text>
    <text class="t" x="832" y="952" font-size="16" fill="#d6d0c2">GOLD <tspan font-size="12">ASTRONUT*</tspan></text>
  </g>

  <rect x="300" y="966" width="620" height="26" rx="4" fill="#1b1b1d"/>
  <text class="t" x="582" y="983" font-size="9.5" font-weight="400">The Text Here is Not Readable. The Text Here is Not Readable. The Text Here is Not Readable.</text>

  <!-- engine start button -->
  <circle cx="152" cy="777" r="40" fill="#3a3a3e" stroke="#c9c9c9" stroke-width="3"/>
  <circle cx="152" cy="777" r="33" fill="#e01515"/>
  <text class="t t-dark" x="152" y="776" font-size="12" font-weight="400">ENGINE</text>
  <text class="t t-dark" x="152" y="789" font-size="12" font-weight="400">START</text>
</svg>
</body>
</html>
```